Web design required

1-We need a web design for existing company based in New Zealand
2-We build residential house and light commercial
3-We has in-house designer which allow us can provide interior design
4-We modeling project before site construction, which enable both client and construction team to visually analysis whole project,

Target Market(s)

middle class residential house market
Ref: http://www.parvellbuilders.co.nz/

Industry/Entity Type

Construction Company

Number of Pages Required

1 page

Font styles to use
Sans Serif
Other font styles liked:
• Such as : Central Gothic or similar which has more design taste

Colors

Designer to choose colors to be used in the design.

Requirements
Must have
• Front sheet, contact information, sample project

```html
<!DOCTYPE html>
<html lang="en">
<head>
<meta charset="utf-8">
<title>Harbourline Homes</title>
<link rel="stylesheet" href="https://fonts.googleapis.com/css2?family=Montserrat:wght@400;500;600;700&family=Jost:wght@400;500&family=Exo+2:wght@500&display=swap">
<style>
:root{
  --blue:#0a4fa6;
  --blue-dark:#083f86;
  --ink:#2a2a2a;
  --text:#333;
  --grey-panel:#5f5f5f;
  --grey-light:#e8e8e8;
  --footer:#3f3f3f;
  --footer-bottom:#333333;
  --rule:#c9c9c9;
  --white:#fff;
}
*{margin:0;padding:0;box-sizing:border-box}
html,body{width:1200px;height:2605px;overflow:hidden}
body{position:relative;background:var(--white);font-family:"Jost",sans-serif;color:var(--text)}
.abs{position:absolute}

/* header */
.top-line{left:0;top:0;width:1200px;height:3px;background:var(--blue)}
.contact-tab{left:728px;top:0;width:350px;height:30px;background:var(--blue);color:var(--white);
  font-size:12px;display:flex;align-items:center;justify-content:center;gap:20px;white-space:nowrap;
  clip-path:polygon(0 0,100% 0,96% 100%,4% 100%)}
.contact-tab span{display:flex;align-items:center;gap:6px}
.brand{left:142px;top:25px;display:flex;align-items:center;gap:12px}
.brand-mark{width:42px;height:42px;background:var(--blue)}
.brand-name{font-family:"Montserrat",sans-serif;font-weight:600;font-size:19px;line-height:21px;color:var(--ink);letter-spacing:2px;text-transform:uppercase}
.nav{left:0;top:60px;width:1200px;font-family:"Montserrat",sans-serif;font-size:13px;font-weight:500;color:var(--ink);letter-spacing:.3px}
.nav a{position:absolute;text-decoration:none;color:inherit;top:0}
.nav a.active{color:var(--blue)}
.nav-active-bg{left:516px;top:42px;width:50px;height:50px;background:#f0f0f0;border-radius:50%}

/* hero */
.hero{left:0;top:104px;width:1200px;height:480px;
  background:linear-gradient(180deg,#4f87d0 0%,#9dbbe0 30%,#b9bdc2 55%,#6f7466 80%,#4a5a3a 100%)}
.hero-caption{left:0;top:530px;width:1200px;height:54px;background:rgba(30,30,30,.55);
  color:var(--white);font-family:"Exo 2",sans-serif;font-size:27px;font-weight:500;
  display:flex;align-items:center;justify-content:center;letter-spacing:.5px}
.hero-arrow{top:300px;width:38px;height:38px;border-radius:50%;border:2px solid rgba(255,255,255,.8);background:rgba(255,255,255,.2)}

/* section headings */
.section-title{left:0;width:1200px;text-align:center;font-family:"Montserrat",sans-serif;font-weight:600;font-size:30px;color:var(--ink);text-transform:uppercase}
.section-title em{font-style:normal;color:var(--blue)}
.divider{height:14px}
.divider svg{display:block}

/* about */
.about-text{left:156px;top:718px;width:888px;text-align:center;font-size:12.2px;line-height:21.5px;color:var(--text)}
.btn{display:flex;align-items:center;justify-content:center;font-family:"Montserrat",sans-serif;font-weight:600;font-size:12px;color:var(--white);text-transform:uppercase;letter-spacing:.3px}
.btn-blue{background:var(--blue)}
.btn-grey{background:var(--grey-panel)}

/* services */
.service{top:917px;width:600px;height:551px}
.service-commercial{left:0;background:var(--blue)}
.service-residential{left:600px;background:var(--grey-panel)}
.service-title{top:974px;font-family:"Montserrat",sans-serif;font-weight:600;font-size:26px;color:var(--white);text-transform:uppercase}
.service-photo{top:1067px;width:428px;height:205px;border:3px solid var(--white)}
.service-text{top:1290px;width:428px;font-size:12.2px;line-height:21.5px;color:var(--white)}

/* projects */
.project{top:1615px;width:216px;height:145px;border:4px solid var(--white);box-shadow:0 0 0 1px #e2e2e2}
.project-overlay{display:flex;flex-direction:column;align-items:center;justify-content:center;gap:8px;color:var(--white);font-size:14px;background:rgba(0,0,0,.35)}
.slider-arrow{width:16px;height:26px}

/* testimonials */
.testimonials{left:0;top:1824px;width:1200px;height:472px;background:var(--grey-light)}
.quote{top:1975px;width:294px;height:113px;background:var(--blue);color:var(--white);font-size:12.2px;line-height:22px;padding:14px 14px}
.quote::after{content:"";position:absolute;left:78px;bottom:-16px;border-left:14px solid transparent;border-right:14px solid transparent;border-top:16px solid var(--blue)}
.avatar{top:2109px;width:66px;height:66px;border-radius:50%;border:3px solid var(--white);background:#8a8f96;box-shadow:0 0 0 1px #bbb}
.client-name{top:2122px;font-family:"Montserrat",sans-serif;font-weight:600;font-size:15px;color:var(--blue);text-transform:uppercase}
.client-role{top:2145px;font-size:13px;color:var(--ink)}
.skyline{left:142px;top:2200px;width:916px;height:96px;background:linear-gradient(180deg,rgba(63,63,63,0) 0%,rgba(63,63,63,.35) 40%,#3f3f3f 100%)}

/* footer */
.footer{left:0;top:2296px;width:1200px;height:266px;background:var(--footer)}
.footer-bottom{left:0;top:2562px;width:1200px;height:43px;background:var(--footer-bottom);border-top:1px solid #555;
  color:#ddd;font-size:11.5px;display:flex;align-items:center;justify-content:center}
.footer-heading{top:2337px;font-family:"Montserrat",sans-serif;font-weight:600;font-size:13px;color:var(--white);text-transform:uppercase}
.footer-heading::after{content:"";display:block;width:44px;height:1px;background:#777;margin-top:9px}
.footer-col-rule{top:2336px;width:1px;height:160px;background:#555}
.quick-links{left:142px;top:2376px;list-style:none;color:var(--white);font-size:12px}
.quick-links li{height:23.5px;display:flex;align-items:center;gap:10px}
.quick-links li::before{content:"»";color:#999;font-size:10px}
.contact-list{left:366px;top:2374px;width:190px;color:var(--white);font-size:12px;line-height:15px}
.contact-list .row{display:flex;gap:10px;margin-bottom:12px}
.contact-list svg{flex:none;margin-top:1px}
.field{left:636px;width:189px;background:var(--white);font-size:11px;font-style:italic;color:#999;padding:5px 7px}
.submit{left:636px;top:2494px;width:70px;height:25px}
.footer-brand{left:900px;top:2420px;width:200px;text-align:center;font-family:"Montserrat",sans-serif;font-weight:600;font-size:16px;color:#cfcfcf;text-transform:uppercase;letter-spacing:1px}
.social{top:2474px;width:22px;height:22px;border-radius:50%;background:#7a7a7a}
</style>
</head>
<body>

<!-- header -->
<div class="abs top-line"></div>
<div class="abs contact-tab">
  <span><svg width="11" height="11" viewBox="0 0 24 24"><path fill="#fff" d="M6.6 10.8a15 15 0 0 0 6.6 6.6l2.2-2.2c.3-.3.7-.4 1-.2 1.1.4 2.3.6 3.6.6.6 0 1 .4 1 1V20c0 .6-.4 1-1 1A17 17 0 0 1 3 4c0-.6.4-1 1-1h3.5c.6 0 1 .4 1 1 0 1.3.2 2.5.6 3.6.1.3 0 .7-.2 1z"/></svg>123 456 7890</span>
  <span><svg width="12" height="10" viewBox="0 0 24 18"><path fill="#fff" d="M0 0h24v18H0z"/><path fill="none" stroke="#0a4fa6" stroke-width="2" d="M1 1l11 9 11-9"/></svg>hello@harbourlinehomes.co.nz</span>
</div>
<div class="abs brand"><div class="brand-mark"></div><div class="brand-name">Harbourline<br>Homes</div></div>
<div class="abs nav-active-bg"></div>
<nav class="abs nav">
  <a class="active" style="left:523px">HOME</a>
  <a style="left:605px">ABOUT US</a>
  <a style="left:713px">SERVICES</a>
  <a style="left:816px">RECENT PROJECTS</a>
  <a style="left:976px">CONTACT US</a>
</nav>

<!-- hero -->
<div class="abs hero" role="img" aria-label="Photo of a couple embracing in front of a modern two-storey family home under a blue sky"></div>
<div class="abs hero-arrow" style="left:86px"></div>
<div class="abs hero-arrow" style="left:1076px"></div>
<div class="abs hero-caption">We Build Residential House And Light Commercial</div>

<!-- about -->
<h2 class="abs section-title" style="top:638px">About <em>Harbourline Homes</em></h2>
<div class="abs divider" style="left:386px;top:690px">
  <svg width="428" height="14"><line x1="0" y1="7" x2="200" y2="7" stroke="#c9c9c9" stroke-width="2" stroke-dasharray="2 3"/><circle cx="214" cy="7" r="7" fill="#9a9a9a"/><line x1="228" y1="7" x2="428" y2="7" stroke="#c9c9c9" stroke-width="2" stroke-dasharray="2 3"/></svg>
</div>
<p class="abs about-text">Lorem ipsum dolor sit amet, consectetuer adipiscing elit, sed diam nonummy nibh euismod tincidunt ut laoreet dolore magna aliquam erat volutpat. Ut wisi enim ad minim veniam, quis nostrud exerci tation ullamcorper suscipit lobortis nisl ut aliquip ex ea commodo consequat. Duis autem vel eum iriure dolor in hendrerit in vulputate velit esse molestie consequat, vel illum dolore eu feugiat nulla facilisis at vero eros et accumsan et iusto odio dignissim qui blandit praesent luptatum zzril delenit augue duis dolore te feugait nulla facilisi nibh euismod tincidunt ut laoreet dolore magna.</p>
<div class="abs btn btn-blue" style="left:551px;top:825px;width:99px;height:30px">Read More</div>

<!-- services -->
<section class="abs service service-commercial"></section>
<section class="abs service service-residential"></section>
<h3 class="abs service-title" style="left:142px">Commercial Services</h3>
<h3 class="abs service-title" style="left:630px">Residential Services</h3>
<div class="abs divider" style="left:142px;top:1021px">
  <svg width="428" height="14"><circle cx="7" cy="7" r="7" fill="#9fb6d8"/><line x1="22" y1="7" x2="428" y2="7" stroke="#7f9ccc" stroke-width="2" stroke-dasharray="2 3"/></svg>
</div>
<div class="abs divider" style="left:630px;top:1021px">
  <svg width="428" height="14"><circle cx="7" cy="7" r="7" fill="#9a9a9a"/><line x1="22" y1="7" x2="428" y2="7" stroke="#888" stroke-width="2" stroke-dasharray="2 3"/></svg>
</div>
<div class="abs service-photo" style="left:142px;background:linear-gradient(180deg,#2a4a8a 0%,#7f8fb5 45%,#d9a86a 70%,#3b3f4a 100%)" role="img" aria-label="Photo of a curved glass commercial building at dusk"></div>
<div class="abs service-photo" style="left:630px;background:linear-gradient(180deg,#2e6fd0 0%,#8fb5e8 40%,#c9c9c4 65%,#5f7a45 100%)" role="img" aria-label="Photo of a two-storey suburban family house with a front lawn"></div>
<p class="abs service-text" style="left:144px">Lorem ipsum dolor sit amet, consectetuer adipiscing elit, sed diam nonummy nibh euismod tincidunt ut laoreet dolore magna aliquam erat volutpat. Ut wisi enimad minim veniam, quis nostrud exerci tation ullamcorper.</p>
<p class="abs service-text" style="left:631px">Lorem ipsum dolor sit amet, consectetuer adipiscing elit, sed diam nonummy nibh euismod tincidunt ut laoreet dolore magna aliquam erat volutpat. Ut wisi enimad minim veniam, quis nostrud exerci tation ullamcorper.</p>
<div class="abs btn btn-grey" style="left:142px;top:1374px;width:99px;height:29px">Read More</div>
<div class="abs btn btn-blue" style="left:628px;top:1374px;width:99px;height:29px">Read More</div>

<!-- recent projects -->
<h2 class="abs section-title" style="top:1522px">Recent <em>Projects</em></h2>
<div class="abs divider" style="left:386px;top:1574px">
  <svg width="428" height="14"><line x1="0" y1="7" x2="200" y2="7" stroke="#c9c9c9" stroke-width="2" stroke-dasharray="2 3"/><circle cx="214" cy="7" r="7" fill="#9a9a9a"/><line x1="228" y1="7" x2="428" y2="7" stroke="#c9c9c9" stroke-width="2" stroke-dasharray="2 3"/></svg>
</div>
<svg class="abs slider-arrow" style="left:102px;top:1674px" viewBox="0 0 16 26"><path d="M13 2L3 13l10 11" fill="none" stroke="#999" stroke-width="2"/></svg>
<svg class="abs slider-arrow" style="left:1082px;top:1674px" viewBox="0 0 16 26"><path d="M3 2l10 11L3 24" fill="none" stroke="#999" stroke-width="2"/></svg>
<div class="abs project" style="left:142px;background:linear-gradient(180deg,#2e72c9 0%,#7fa7d8 45%,#3a4f6e 75%,#6b7060 100%)" role="img" aria-label="Photo of a modern glass office block"></div>
<div class="abs project" style="left:375px;background:linear-gradient(180deg,#3d7ed4 0%,#a8c6ea 40%,#dadada 65%,#5c7b3e 100%)" role="img" aria-label="Photo of a white weatherboard family home"></div>
<div class="abs project" style="left:608px;background:linear-gradient(180deg,#2c3640 0%,#4a5560 55%,#3f4a38 100%)" role="img" aria-label="Photo of a dark-clad contemporary home">
  <div class="project-overlay" style="position:absolute;inset:0">
    <svg width="32" height="32" viewBox="0 0 32 32"><circle cx="16" cy="16" r="14" fill="none" stroke="#fff" stroke-width="1.5"/><path d="M16 9v14M9 16h14" stroke="#fff" stroke-width="1.5"/></svg>
    <span>Laoreet Dolore Magna</span>
  </div>
</div>
<div class="abs project" style="left:841px;background:linear-gradient(180deg,#4d8ad8 0%,#b6cdea 40%,#c8b79a 65%,#6a8a4a 100%)" role="img" aria-label="Photo of a street of suburban houses"></div>

<!-- testimonials -->
<section class="abs testimonials"></section>
<h2 class="abs section-title" style="top:1877px">Client <em>Testimonials</em></h2>
<div class="abs divider" style="left:386px;top:1930px">
  <svg width="428" height="14"><line x1="0" y1="7" x2="200" y2="7" stroke="#c4c4c4" stroke-width="2" stroke-dasharray="2 3"/><circle cx="214" cy="7" r="7" fill="#9a9a9a"/><line x1="228" y1="7" x2="428" y2="7" stroke="#c4c4c4" stroke-width="2" stroke-dasharray="2 3"/></svg>
</div>
<svg class="abs slider-arrow" style="left:102px;top:2016px" viewBox="0 0 16 26"><path d="M13 2L3 13l10 11" fill="none" stroke="#999" stroke-width="2"/></svg>
<svg class="abs slider-arrow" style="left:1082px;top:2016px" viewBox="0 0 16 26"><path d="M3 2l10 11L3 24" fill="none" stroke="#999" stroke-width="2"/></svg>

<div class="abs quote" style="left:142px">Lorem ipsum dolor sit amet, consectetuer adipig elit, sed diam nonummy nibh euismod tincidunt ut laoreet dolore magna aliquam volutpat.</div>
<div class="abs quote" style="left:453px">Lorem ipsum dolor sit amet, consectetuer adipig elit, sed diam nonummy nibh euismod tincidunt ut laoreet dolore magna aliquam volutpat.</div>
<div class="abs quote" style="left:764px">Lorem ipsum dolor sit amet, consectetuer adipig elit, sed diam nonummy nibh euismod tincidunt ut laoreet dolore magna aliquam volutpat.</div>

<div class="abs avatar" style="left:152px" role="img" aria-label="Client portrait"></div>
<div class="abs avatar" style="left:463px" role="img" aria-label="Client portrait"></div>
<div class="abs avatar" style="left:774px" role="img" aria-label="Client portrait"></div>
<div class="abs client-name" style="left:233px">Lorem Ipsum</div>
<div class="abs client-role" style="left:233px">Lorem ipsum dolor sit amet</div>
<div class="abs client-name" style="left:544px">Lorem Ipsum</div>
<div class="abs client-role" style="left:544px">Lorem ipsum dolor sit amet</div>
<div class="abs client-name" style="left:855px">Lorem Ipsum</div>
<div class="abs client-role" style="left:855px">Lorem ipsum dolor sit amet</div>

<div class="abs skyline" role="img" aria-label="Illustrated row of construction silhouettes: trucks, workers, crane, houses and buildings"></div>

<!-- footer -->
<footer class="abs footer"></footer>
<div class="abs footer-col-rule" style="left:307px"></div>
<div class="abs footer-col-rule" style="left:575px"></div>
<div class="abs footer-col-rule" style="left:886px"></div>

<div class="abs footer-heading" style="left:142px">Quick Links</div>
<ul class="abs quick-links">
  <li>Home</li><li>About Us</li><li>Services</li><li>Recent Projects</li><li>Contact Us</li>
</ul>

<div class="abs footer-heading" style="left:366px">Contact Details</div>
<div class="abs contact-list">
  <div class="row"><svg width="10" height="14" viewBox="0 0 10 14"><path fill="#fff" d="M5 0a5 5 0 0 1 5 5c0 3.5-5 9-5 9S0 8.5 0 5a5 5 0 0 1 5-5z"/><circle cx="5" cy="5" r="2" fill="#3f3f3f"/></svg><div>HARBOURLINE HOMES<br>12 Harbour Road, Devonport<br>Auckland 0624</div></div>
  <div class="row"><svg width="11" height="11" viewBox="0 0 24 24"><path fill="#fff" d="M6.6 10.8a15 15 0 0 0 6.6 6.6l2.2-2.2c.3-.3.7-.4 1-.2 1.1.4 2.3.6 3.6.6.6 0 1 .4 1 1V20c0 .6-.4 1-1 1A17 17 0 0 1 3 4c0-.6.4-1 1-1h3.5c.6 0 1 .4 1 1 0 1.3.2 2.5.6 3.6.1.3 0 .7-.2 1z"/></svg><div>123.456.7890</div></div>
  <div class="row"><svg width="12" height="11" viewBox="0 0 12 11"><rect x="2" y="0" width="8" height="3" fill="#fff"/><rect x="0" y="3" width="12" height="5" fill="#fff"/><rect x="2" y="7" width="8" height="4" fill="#fff" stroke="#3f3f3f"/></svg><div>123.456.7890</div></div>
  <div class="row"><svg width="12" height="10" viewBox="0 0 24 18"><path fill="#fff" d="M0 0h24v18H0z"/><path fill="none" stroke="#3f3f3f" stroke-width="2" d="M1 1l11 9 11-9"/></svg><div style="font-size:10.5px">hello@harbourlinehomes.co.nz</div></div>
</div>

<div class="abs footer-heading" style="left:636px">Quick Inquiry</div>
<div class="abs field" style="top:2380px;height:26px">Name</div>
<div class="abs field" style="top:2411px;height:26px">Email</div>
<div class="abs field" style="top:2442px;height:42px">Message</div>
<div class="abs btn btn-blue submit">Submit</div>

<div class="abs footer-brand">Harbourline Homes</div>
<div class="abs social" style="left:945px"></div>
<div class="abs social" style="left:974px"></div>
<div class="abs social" style="left:1003px"></div>
<div class="abs social" style="left:1032px"></div>

<div class="abs footer-bottom">Copyright © 2017 HARBOURLINE HOMES. All Rights Reserved.</div>

</body>
</html>
```